Need website redesign!

I have a site, www.mapleridgefitcamp.example

I am looking to have it redesigned to make it simpler, and encourage people who hit the home page to click on a service, opt in, or contact me for more info. Having a video front and center with icons representing the services we offer around it may be a good idea, but I am open to YOUR design. Conversion is my goal. I want it to be friendly, but convey the fun and ENERGY of my bootcamp. Scrolling pics on home page so people can get a feel for our bootcamp is recommended as well.

```html
<!DOCTYPE html>
<html lang="en">
<head>
<meta charset="utf-8">
<title>Maple Ridge Fit Camp</title>
<link href="https://fonts.googleapis.com/css2?family=Raleway:wght@400;500;600;700&family=Open+Sans:wght@400;600&display=swap" rel="stylesheet">
<style>
:root{
  --red:#e0140f;
  --red-dark:#a90d0a;
  --black:#000;
  --charcoal:#222;
  --panel:#1c1c1c;
  --card:#2a2a2a;
  --text:#fff;
  --muted:#9a9a9a;
  --blue:#2aa7e6;
}
*{margin:0;padding:0;box-sizing:border-box}
html,body{width:808px;height:1200px;overflow:hidden;background:var(--black)}
body{position:relative;font-family:"Open Sans",sans-serif;color:var(--text)}
.abs{position:absolute}
.topbar{left:0;top:0;width:808px;height:50px;background:var(--charcoal)}
.navband{left:0;top:50px;width:808px;height:29px;background:linear-gradient(#ec2a1f,#c50f0a)}
.logo{left:94px;top:0;width:103px;height:98px;background:#000;display:flex;flex-direction:column;align-items:center;justify-content:center;text-align:center;font-family:"Raleway",sans-serif;font-weight:700;color:var(--red);font-size:13px;line-height:1.15;z-index:3;box-shadow:0 2px 6px rgba(0,0,0,.6)}
.logo small{display:block;font-size:5px;color:var(--red);margin-top:6px;font-weight:700}
.nav{left:270px;top:50px;height:29px;display:flex;z-index:2}
.nav a{font-family:"Raleway",sans-serif;font-size:10.5px;font-weight:500;color:#fff;text-decoration:none;padding:0 14px;line-height:29px;border-right:1px solid rgba(255,255,255,.35)}
.nav a:last-child{border-right:0}
.hero{left:0;top:79px;width:808px;height:293px;background:linear-gradient(90deg,#7a4a36 0%,#b9a79a 30%,#3a78b8 65%,#d8d0c8 100%)}
.caption{left:94px;top:166px;width:263px;height:111px;background:rgba(30,30,30,.88);padding:18px 22px}
.caption .kicker{font-family:"Raleway",sans-serif;color:var(--red);font-size:14px;font-weight:600}
.caption h1{font-family:"Raleway",sans-serif;font-size:20px;font-weight:600;margin-top:3px}
.caption p{font-size:6.5px;line-height:1.8;color:#ddd;margin-top:6px}
.dots{left:388px;top:355px;display:flex;gap:4px}
.dots i{width:8px;height:8px;border-radius:50%;background:#fff;display:block}
.card{top:389px;width:200px;height:152px;background:var(--card);border:1px solid #333}
.card .img{height:93px}
.card h3{font-family:"Raleway",sans-serif;font-size:12px;font-weight:500;margin:10px 14px 3px}
.card p{font-size:6.3px;line-height:1.9;color:var(--muted);margin:0 14px}
.optin{left:513px;top:389px;width:201px;height:152px;background:linear-gradient(#e51d16,#b80d09);padding:14px 20px}
.optin p{font-family:"Raleway",sans-serif;font-size:9.5px;line-height:1.55}
.optin b{font-size:11px;font-weight:600}
.field{height:18px;background:#fff;margin-top:6px;font-size:6px;color:#777;padding:0 8px;line-height:18px}
.btn{background:linear-gradient(#d5130e,#8d0a07);font-family:"Raleway",sans-serif;font-weight:600;font-size:8.5px;text-align:center;color:#fff}
.optin .btn{height:22px;line-height:22px;margin-top:6px}
.about{left:0;top:565px;width:808px;height:221px;background:linear-gradient(#262626,#141414)}
.about h2{left:98px;top:600px;font-family:"Raleway",sans-serif;font-size:17px;font-weight:500;line-height:1.45;letter-spacing:.3px}
.about h2 span{color:var(--blue)}
.about-text{left:98px;top:651px;width:345px;font-size:6.3px;line-height:1.9;color:var(--muted)}
.about-text p+p{margin-top:5px}
.learn{left:98px;top:722px;width:83px;height:23px;line-height:23px;background:var(--red);font-size:8px}
.video{left:478px;top:600px;width:238px;height:143px;background:linear-gradient(135deg,#cfc6bd,#8fa3b6 55%,#6d6b7a)}
.play{left:580px;top:655px}
.blog-title{left:94px;top:817px;font-family:"Raleway",sans-serif;font-size:15px;font-weight:500}
.post{width:310px;height:112px}
.post .thumb{position:absolute;left:0;top:0;width:111px;height:110px}
.post h4{position:absolute;left:120px;top:2px;width:185px;font-size:7.8px;font-weight:600;line-height:1.5}
.post p{position:absolute;left:120px;top:42px;width:180px;font-size:6.3px;line-height:1.9;color:var(--muted)}
.post .btn{position:absolute;left:120px;top:91px;width:75px;height:21px;line-height:21px;background:var(--red);font-size:7.5px;font-weight:500}
.footer{left:0;top:1136px;width:808px;height:64px;background:#1a1a1a}
.flinks{left:94px;top:1153px;font-family:"Raleway",sans-serif;font-size:8.5px;font-weight:600}
.flinks span{margin:0 5px;font-weight:400}
.copy{left:94px;top:1170px;font-size:6.4px;color:var(--muted)}
.social{left:641px;top:1153px;display:flex;gap:8px}
.social i{display:block;width:15px;height:15px;border-radius:3px;background:#d8d8d8}
</style>
</head>
<body>
<div class="abs topbar"></div>
<div class="abs navband"></div>
<div class="abs logo">MAPLE RIDGE<br>FIT CAMP<small>MAPLERIDGEFITCAMP.EXAMPLE</small></div>
<nav class="abs nav">
  <a>HOME</a><a>SERVICES</a><a>CLASSES</a><a>ABOUT US</a><a>FAQ'S</a><a>CONTACT US</a>
</nav>

<div class="abs hero" role="img" aria-label="Group of people doing lunges in a brick-walled gym"></div>
<div class="abs caption">
  <div class="kicker">MAURIS VEL LACUS VITAE</div>
  <h1>VIVAMUS PORTTITOR</h1>
  <p>Mauris vel lacus vitae felis vestibulum volutpat massa Etiam eu urna Sed porta Suspendisse quam leo molestie sed</p>
</div>
<div class="abs dots"><i></i><i></i><i></i><i></i></div>

<div class="abs card" style="left:94px">
  <div class="img" role="img" aria-label="Woman doing a push-up in a gym" style="background:linear-gradient(135deg,#e8e4e0,#c9a6a8 60%,#6d6060)"></div>
  <h3>ABOUT CLASSES</h3>
  <p>Etiam eu urna Sed porta Suspendisse quam leo molestie sed luctus quis feugiat in pede Fusce</p>
</div>
<div class="abs card" style="left:304px">
  <div class="img" role="img" aria-label="Man stretching outdoors at sunrise" style="background:linear-gradient(#dfe6ea,#d9b47a 55%,#6a5038)"></div>
  <h3>LOCATIONS</h3>
  <p>Etiam eu urna Sed porta Suspendisse quam leo molestie sed luctus quis feugiat in pede Fusce</p>
</div>
<div class="abs optin">
  <p>Leave your email for a<br>FREE week of bootcamp,<br><b>NO OBLIGATION</b></p>
  <div class="field">Your Name</div>
  <div class="field">Email address</div>
  <div class="btn">GET STARTED NOW</div>
</div>

<section class="abs about"></section>
<div class="about">
  <h2 class="abs">WHAT IS MAPLE RIDGE<br><span>&amp; FIT CAMP BOOTCAMP</span></h2>
  <div class="abs about-text">
    <p>dis parturient montes nascetur ridiculus mus In iaculis facilisis massa Etiam eu urna Sed porta Suspendisse quam leo molestie sed luctus quis feugiat in pede Fusce tellus Sed metus augue convallis et vehicula ut pulvinar eu ante Integer orci tellus tristique diam mauris viverra in gravida eu mattis in ante</p>
    <p>Morbi eget arcu Morbi porta libero id ullamcorper nonummy nibh ligula pulvinar metus eget consectetuer augue nisi quis lacus Ut ac mi quis lacus mollis aliquam Curabitur iaculis tempus eros</p>
  </div>
  <div class="abs btn learn">LEARN MORE</div>
  <div class="abs video" role="img" aria-label="Video still of a smiling group of bootcamp members in a gym"></div>
  <svg class="abs play" width="34" height="34" viewBox="0 0 34 34"><circle cx="17" cy="17" r="16" fill="#fff"/><path d="M13 10v14l11-7z" fill="#111"/></svg>
</div>

<h2 class="abs blog-title">Recent Blog</h2>
<article class="abs post" style="left:94px;top:850px">
  <div class="thumb" role="img" aria-label="Members training with suspension straps" style="background:linear-gradient(135deg,#d9d9d9,#7b7f86 60%,#2d3340)"></div>
  <h4>If you're in Northern Cedar County, Maple Ridge, Alder Falls, Brookvale, Pinecrest or Westhaven, come and check out the camp</h4>
  <p>Dis parturient montes nascetur ridiculus mus In iaculis facilisis massa Etiam eu urna Sed porta Suspendisse quam leo molestie sed luctus quis feugiat in pede Fusce tellus Sed metus augue convallis</p>
  <div class="btn">CLICK HERE</div>
</article>
<article class="abs post" style="left:418px;top:851px">
  <div class="thumb" role="img" aria-label="Woman doing crunches on a mat in a gym" style="background:linear-gradient(#c8d3d8,#6f8a6a 60%,#3a3a3a)"></div>
  <h4>If you're in Northern Cedar County, Maple Ridge, Alder Falls, Brookvale, Pinecrest or Westhaven, come and check out the camp</h4>
  <p>Dis parturient montes nascetur ridiculus mus In iaculis facilisis massa Etiam eu urna Sed porta Suspendisse quam leo molestie sed luctus quis feugiat in pede Fusce tellus Sed metus augue convallis</p>
  <div class="btn">CLICK HERE</div>
</article>
<article class="abs post" style="left:93px;top:990px">
  <div class="thumb" role="img" aria-label="Bootcamp group posing in a forest" style="background:linear-gradient(#b7c48a,#5f7a3c 55%,#5a4a3a)"></div>
  <h4>If you're in Northern Cedar County, Maple Ridge, Alder Falls, Brookvale, Pinecrest or Westhaven, come and check out the camp</h4>
  <p>Dis parturient montes nascetur ridiculus mus In iaculis facilisis massa Etiam eu urna Sed porta Suspendisse quam leo molestie sed luctus quis feugiat in pede Fusce tellus Sed metus augue convallis</p>
  <div class="btn">CLICK HERE</div>
</article>
<article class="abs post" style="left:417px;top:991px">
  <div class="thumb" role="img" aria-label="Woman lifting a dumbbell" style="background:linear-gradient(135deg,#c9b5a5,#56677a 60%,#2a2f38)"></div>
  <h4>If you're in Northern Cedar County, Maple Ridge, Alder Falls, Brookvale, Pinecrest or Westhaven, come and check out the camp</h4>
  <p>Dis parturient montes nascetur ridiculus mus In iaculis facilisis massa Etiam eu urna Sed porta Suspendisse quam leo molestie sed luctus quis feugiat in pede Fusce tellus Sed metus augue convallis</p>
  <div class="btn">CLICK HERE</div>
</article>

<footer class="abs footer"></footer>
<div class="abs flinks">HOME<span>|</span>SERVICES<span>|</span>CLASSES<span>|</span>ABOUT US<span>|</span>FAQ'S<span>|</span>CONTACT US</div>
<div class="abs copy">© 2015 Company Name &nbsp;All right reserved &nbsp;Term of Use</div>
<div class="abs social"><i aria-label="Social link"></i><i aria-label="Social link"></i><i aria-label="Social link"></i></div>
</body>
</html>
```